Business Cards for a law firm

Business cards for our law firm. Use our silhoette logo and OAK PARTNERS - check our website (www.oakpartners.example)

Contact Information for Business Card

our silhouette logo, OAK PARTNERS, 800-555-0147, Dorian Pemberton, dorian@oakpartners.example

Requirements
Must have
• our silhouette logo, OAK PARTNERS, 800-555-0147, Dorian Pemberton, dorian@oakpartners.example

```html
<!DOCTYPE html>
<html lang="en">
<head>
<meta charset="utf-8">
<title>Oak Partners Business Cards</title>
<link href="https://fonts.googleapis.com/css2?family=Cinzel:wght@600;700&family=Open+Sans:wght@400&display=swap" rel="stylesheet">
<style>
  :root {
    --navy: #1b2f6b;
    --white: #ffffff;
    --stage: #2b2b2d;
    --ink-grey: #555a63;
    --rule-grey: #c9ccd2;
    --ghost-grey: #eceef1;
    --band-black: #1a1a1a;
  }
  * { margin: 0; padding: 0; box-sizing: border-box; }
  html, body { width: 1200px; height: 874px; overflow: hidden; }
  body { background: var(--stage); position: relative; }

  .card {
    position: absolute;
    left: 280px;
    width: 640px;
    height: 366px;
    border-radius: 22px;
    overflow: hidden;
    box-shadow: 0 10px 28px rgba(0,0,0,0.45);
  }
  .card--front { top: 48px; background: var(--navy); }
  .card--back { top: 460px; background: var(--white); }

  .brand {
    font-family: "Cinzel", serif;
    font-weight: 700;
    letter-spacing: 0.08em;
    white-space: nowrap;
    display: flex;
    align-items: center;
    gap: 14px;
  }
  .brand-mark { display: block; width: 16px; height: 16px; background: currentColor; }

  .card--front .brand {
    position: absolute; left: 160px; top: 160px;
    font-size: 36px; color: var(--white);
  }

  .ghost-figures {
    position: absolute; left: 70px; top: 14px;
    width: 200px; height: 300px;
    background: linear-gradient(180deg, var(--ghost-grey), rgba(236,238,241,0.55));
    border-radius: 60px 60px 0 0;
  }

  .card--back .brand {
    position: absolute; left: 330px; top: 96px;
    font-size: 26px; color: var(--navy);
  }

  .holder-name {
    position: absolute; left: 58px; top: 150px;
    font-family: "Cinzel", serif; font-weight: 700;
    font-size: 24px; letter-spacing: 0.04em; color: var(--navy);
  }

  .contact-list {
    position: absolute; left: 58px; top: 192px;
    list-style: none;
    font-family: "Open Sans", sans-serif; font-size: 14px; color: var(--ink-grey);
  }
  .contact-list li { display: flex; align-items: center; gap: 10px; height: 21px; }
  .contact-list svg { width: 13px; height: 13px; fill: var(--navy); flex: none; }

  .divider {
    position: absolute; left: 58px; top: 270px;
    width: 540px; height: 1px; background: var(--rule-grey);
  }

  .base-line { position: absolute; left: 0; top: 318px; width: 100%; height: 4px; background: var(--band-black); }
  .base-band { position: absolute; left: 0; top: 328px; width: 100%; height: 38px; background: var(--navy); }
</style>
</head>
<body>

<section class="card card--front">
  <div class="brand"><span class="brand-mark"></span>OAK PARTNERS</div>
</section>

<section class="card card--back">
  <div class="ghost-figures" role="img" aria-label="Faint background silhouettes of two standing figures"></div>

  <div class="brand"><span class="brand-mark"></span>OAK PARTNERS</div>

  <h1 class="holder-name">Dorian Pemberton</h1>

  <ul class="contact-list">
    <li>
      <svg viewBox="0 0 24 24" aria-hidden="true"><path d="M6.6 10.8a15 15 0 0 0 6.6 6.6l2.2-2.2c.3-.3.7-.4 1-.2 1.1.4 2.3.6 3.6.6.6 0 1 .4 1 1V20c0 .6-.4 1-1 1A17 17 0 0 1 3 4c0-.6.4-1 1-1h3.5c.6 0 1 .4 1 1 0 1.3.2 2.5.6 3.6.1.3 0 .7-.2 1z"/></svg>
      800-555-0147
    </li>
    <li>
      <svg viewBox="0 0 24 24" aria-hidden="true"><path d="M2 5h20v14H2z M3 6l9 7 9-7" fill="none" stroke="#1b2f6b" stroke-width="2"/><path d="M2 5h20l-10 8z"/></svg>
      dorian@oakpartners.example
    </li>
    <li>
      <svg viewBox="0 0 24 24" aria-hidden="true"><circle cx="12" cy="12" r="10"/><path d="M2 12h20M12 2c3 3 3 17 0 20M12 2c-3 3-3 17 0 20" fill="none" stroke="#ffffff" stroke-width="1.4"/></svg>
      www.oakpartners.example
    </li>
  </ul>

  <div class="divider"></div>
  <div class="base-line"></div>
  <div class="base-band"></div>
</section>

</body>
</html>
```